Basic business card

use my newly created logo - and the phrases (Lower Cost of Test & Accelarated New Product Introduction) - and my new email domain / ID - use at conferences / tradeshows

Industry/Entity Type

semiconductor

Contact Information for Business Card

Daniel K Forde, Owner, communicate via Logo - Lower COT - Cost of Test, Accelerated NPI - New Product Introduction, phone +1 555 613 0946, Chandler, Arizona, USA, daniel.forde@qal-vub.com

Font styles to use
Sans Serif

Requirements
Nice to have
• re-use my logo created via Pixel Harbor last August (#7315926)

```html
<!DOCTYPE html>
<html lang="en">
<head>
<meta charset="utf-8">
<title>QAL-VUB Business Card</title>
<link href="https://fonts.googleapis.com/css2?family=Open+Sans:wght@400;600;700&display=swap" rel="stylesheet">
<style>
  :root {
    --stage: #202020;
    --navy: #1f2938;
    --navy-deep: #121a25;
    --navy-light: #2b3a4d;
    --slate: #48516b;
    --divider: #1a2230;
    --orange: #ef9020;
    --blue: #1f7fc8;
    --white: #f2f4f7;
    --logo-faint: #3b4659;
    --logo-steel: #b9cbe0;
  }
  * { margin: 0; padding: 0; box-sizing: border-box; }
  html, body { width: 1200px; height: 779px; overflow: hidden; background: var(--stage); }
  body { font-family: "Open Sans", Arial, sans-serif; position: relative; }
  .card {
    position: absolute;
    width: 550px;
    height: 314px;
    top: 232px;
    border-radius: 3px;
    overflow: hidden;
    box-shadow: 0 14px 40px rgba(0,0,0,.55);
  }
  .card-front { left: 34px; background: var(--navy); }
  .card-back {
    left: 616px;
    background: radial-gradient(ellipse at 62% 62%, var(--navy-light) 0%, var(--navy) 45%, var(--navy-deep) 100%);
    display: flex; align-items: center; justify-content: center;
  }
  .card-art { position: absolute; inset: 0; }
  .brand-faint {
    position: absolute; left: 26px; top: 18px;
    font-size: 40px; font-weight: 400; letter-spacing: 1px;
    color: var(--logo-faint);
  }
  .brand-main {
    font-size: 66px; font-weight: 600; letter-spacing: 2px;
    color: var(--logo-steel);
  }
  .holder { position: absolute; right: 24px; top: 104px; text-align: right; }
  .holder-name { font-size: 27px; font-weight: 700; line-height: 1.1; }
  .holder-name .first { color: var(--orange); }
  .holder-name .last { color: var(--blue); }
  .holder-title { font-size: 13px; color: var(--white); margin-top: 2px; }
  .contact {
    position: absolute; right: 96px; top: 208px;
    text-align: right; color: var(--white);
    font-size: 13.5px; line-height: 17px;
    list-style: none;
  }
  .contact li { display: flex; justify-content: flex-end; align-items: center; gap: 7px; }
  .contact .gap { margin-top: 8px; }
  .contact svg { width: 12px; height: 12px; flex: none; }
  .contact .spacer { width: 12px; flex: none; }
</style>
</head>
<body>

<section class="card card-front">
  <svg class="card-art" viewBox="0 0 550 314" preserveAspectRatio="none">
    <path d="M0,110 C15,205 95,222 200,208 C300,195 400,170 460,185 C500,200 515,270 520,314 L0,314 Z" fill="var(--slate)"/>
    <path d="M0,110 C15,205 95,222 200,208 C300,195 400,170 460,185" fill="none" stroke="var(--divider)" stroke-width="6"/>
    <path d="M4,94 C18,190 95,206 200,193 C300,180 380,158 440,162" fill="none" stroke="var(--orange)" stroke-width="5" stroke-linecap="round"/>
    <rect x="538" y="130" width="12" height="30" fill="var(--orange)"/>
  </svg>

  <div class="brand-faint">QAL-VUB</div>

  <div class="holder">
    <h1 class="holder-name"><span class="first">Lena</span> <span class="last">Marovic</span></h1>
    <p class="holder-title">Managing Director</p>
  </div>

  <ul class="contact">
    <li>740 Orchard Ln. Suite 310<span class="spacer"></span></li>
    <li>Chandler, AZ 85226<span class="spacer"></span></li>
    <li class="gap">(555) 613-0946
      <svg viewBox="0 0 24 24"><path fill="var(--white)" d="M6.6 10.8a15 15 0 0 0 6.6 6.6l2.2-2.2c.3-.3.7-.4 1-.2 1.1.4 2.3.6 3.6.6.6 0 1 .4 1 1V20c0 .6-.4 1-1 1A17 17 0 0 1 3 4c0-.6.4-1 1-1h3.5c.6 0 1 .4 1 1 0 1.3.2 2.5.6 3.6.1.3 0 .7-.2 1z"/></svg>
    </li>
    <li>hello@qal-vub.com
      <svg viewBox="0 0 24 24"><rect x="2" y="5" width="20" height="14" rx="2" fill="var(--white)"/><path d="M3 6l9 7 9-7" fill="none" stroke="var(--slate)" stroke-width="2"/></svg>
    </li>
    <li>www.qal-vub.com
      <svg viewBox="0 0 24 24"><circle cx="12" cy="12" r="10" fill="var(--white)"/><path d="M2 12h20M12 2c3 3 3 17 0 20M12 2c-3 3-3 17 0 20" fill="none" stroke="var(--slate)" stroke-width="1.6"/></svg>
    </li>
  </ul>
</section>

<section class="card card-back">
  <div class="brand-main">QAL-VUB</div>
</section>

</body>
</html>
```